Business card por a urban DJ, up scale audience target

Need a sober design, modern, conservative colors but i can consider some options, y play rnb, hip hop, EDM and top40.

Business card for contact and personal info, double sided, use logo attrached please; im 42 so i need a card acording to my age an target audience.

Target Market(s)

Adult people, up scale audience

Industry/Entity Type

Music Download

Contact Information for Business Card

Cel (318) 4207265518 www.lumadrift.com

Requirements
Must have
• open mind
Nice to have
• open mind
Should not have
• DJ

```html
<!DOCTYPE html>
<html lang="en">
<head>
<meta charset="utf-8">
<title>Luma Business Card</title>
<link href="https://fonts.googleapis.com/css2?family=Jost:wght@400;500;700&display=swap" rel="stylesheet">
<style>
  :root {
    --backdrop: #3b3e43;
    --card-black: #141414;
    --card-white: #f7f7f7;
    --ink-light: #ffffff;
    --ink-dark: #141414;
  }
  * { margin: 0; padding: 0; box-sizing: border-box; }
  html, body {
    width: 1200px; height: 750px; overflow: hidden;
    background: var(--backdrop);
    font-family: "Jost", sans-serif;
  }
  .stage { position: relative; width: 1200px; height: 750px; }
  .card {
    position: absolute; top: 228px;
    width: 461px; height: 263px;
    overflow: hidden;
    box-shadow: 0 3px 8px rgba(0,0,0,0.45);
  }
  .card--front { left: 124px; background: var(--card-white); }
  .card--back { left: 618px; background: var(--card-black); }

  .brand {
    display: flex; align-items: flex-end; justify-content: center; gap: 10px;
    font-weight: 700; letter-spacing: 4px; line-height: 1;
  }
  .brand__mark { width: 18px; height: 18px; margin-bottom: 52px; }
  .brand__name { font-size: 72px; }

  .front__logo {
    height: 175px; display: flex; align-items: center; justify-content: center;
    color: var(--ink-dark);
  }
  .front__logo .brand__mark { background: var(--ink-dark); }

  .front__info {
    height: 88px; background: var(--card-black); color: var(--ink-light);
    display: flex; flex-direction: column; align-items: center; justify-content: center;
    gap: 4px;
  }
  .info__name { font-size: 21px; font-weight: 500; }
  .info__role { font-size: 17px; font-weight: 400; }
  .info__contact { font-size: 16px; font-weight: 400; }
  .info__divider { margin: 0 6px; }

  .back__content {
    height: 100%; display: flex; flex-direction: column;
    align-items: center; justify-content: center; gap: 10px;
    color: var(--ink-light);
  }
  .back__content .brand__mark { background: var(--ink-light); }
  .back__url { font-size: 11px; font-weight: 700; letter-spacing: 2.4px; }
</style>
</head>
<body>
<main class="stage">
  <section class="card card--front">
    <div class="front__logo">
      <div class="brand">
        <span class="brand__name">LUMA</span>
        <span class="brand__mark"></span>
      </div>
    </div>
    <div class="front__info">
      <p><span class="info__name">MARCO VALE</span> <span class="info__role">- CEO/FOUNDER</span></p>
      <p class="info__contact">(318) 4207265518<span class="info__divider">|</span>www.lumadrift.com</p>
    </div>
  </section>

  <section class="card card--back">
    <div class="back__content">
      <div class="brand">
        <span class="brand__name">LUMA</span>
        <span class="brand__mark"></span>
      </div>
      <p class="back__url">WWW.LUMADRIFT.COM</p>
    </div>
  </section>
</main>
</body>
</html>
```